New business card for a regional office of a US M&A company

We need business card for a finance company, office based in Hong Kong , our Head office is in US, our business is to Merge and acquires companies , the new office will be a regional office for the Asia Pacific region. We want to use the head office logo as attached ( but don't have to be exactly the same, can be a variation to it) as a base and then add Asia Pacific alongside the logo.
We would prefer to have be bilingual Eng + Chinese, although we don't really have Chinese company name .

Industry/Entity Type

Business

Contact Information for Business Card

Clara Jo Tsang
 

VP,
APAC M&A Operations
Orin Vantage Asia Pacific Limited
 
Unit 1407, K18
18 Tai Lok Shan Road, 
Hong Kong 
 
M: +852 6038 1742
T : +852 2836 4100
F : +852 2836 4177
VOIP: 4158
 
cjtsang@orinvantage.com

Font styles to use
Serif
Sans Serif

Colors

Designer to choose colors to be used in the design.

Requirements
Must have
• APAC Office

```html
<!DOCTYPE html>
<html lang="en">
<head>
<meta charset="utf-8">
<title>Orin Vantage Asia Pacific – Business Card</title>
<link href="https://fonts.googleapis.com/css2?family=Open+Sans:wght@700&family=Roboto:wght@400&family=Roboto+Condensed:wght@700&display=swap" rel="stylesheet">
<style>
  :root {
    --backdrop: #6e4a31;
    --navy: #0e2742;
    --cyan: #1fadd2;
    --cyan-bright: #29abd6;
    --white: #ffffff;
    --soft-white: #e3e8ee;
    --paper: #f1f3f5;
  }
  * { box-sizing: border-box; margin: 0; padding: 0; }
  html, body {
    width: 1200px; height: 960px; overflow: hidden;
    background: var(--backdrop);
  }
  .canvas { position: relative; width: 1200px; height: 960px; }

  .card { position: absolute; width: 600px; height: 343px; box-shadow: 0 3px 8px rgba(0,0,0,.35); overflow: hidden; }
  .card-front { left: 314px; top: 113px; background: var(--navy); }
  .card-back { left: 311px; top: 472px; background: var(--cyan); }

  /* Front */
  .brand-block { position: absolute; left: 40px; top: 136px; width: 266px; text-align: center; }
  .brand-square { display: block; width: 30px; height: 30px; margin: 0 auto 18px; background: var(--cyan); }
  .brand-name {
    font-family: "Open Sans", sans-serif; font-weight: 700;
    font-size: 31px; line-height: 1; color: var(--cyan); letter-spacing: .3px; white-space: nowrap;
  }
  .divider {
    position: absolute; left: 319px; top: 56px; width: 1.5px; height: 272px;
    background: linear-gradient(to bottom, rgba(255,255,255,0), rgba(255,255,255,.55) 50%, rgba(255,255,255,0));
  }
  .contact { position: absolute; left: 349px; top: 58px; font-family: "Roboto", sans-serif; color: var(--soft-white); }
  .contact-name {
    font-family: "Roboto Condensed", sans-serif; font-weight: 700;
    font-size: 21px; color: var(--cyan-bright); line-height: 24px; text-transform: uppercase;
  }
  .contact-title { font-size: 15px; color: var(--white); margin: 2px 0 0 2px; line-height: 20px; }
  .address { margin-top: 9px; font-size: 14.5px; line-height: 18.6px; }
  .phones { margin-top: 9px; list-style: none; font-size: 14.5px; line-height: 19px; }
  .phones li { display: flex; align-items: center; gap: 8px; }
  .phones svg { width: 14px; height: 14px; fill: var(--cyan-bright); flex: none; }
  .voip { margin-top: 9px; font-size: 14.5px; }

  .stripe { position: absolute; left: 0; bottom: 0; width: 600px; height: 13px; }

  /* Back */
  .back-brand { position: absolute; left: 0; top: 120px; width: 600px; text-align: center; }
  .back-square { display: block; width: 44px; height: 44px; margin: 0 auto 22px; background: var(--paper); }
  .back-name {
    font-family: "Open Sans", sans-serif; font-weight: 700;
    font-size: 40px; line-height: 1; color: var(--paper); white-space: nowrap;
  }
  .website {
    position: absolute; left: 0; top: 284px; width: 600px; text-align: center;
    font-family: "Roboto", sans-serif; font-size: 14px; letter-spacing: 6.2px; color: #e6f4f9;
  }
</style>
</head>
<body>
<main class="canvas">
  <section class="card card-front" aria-label="Business card front">
    <div class="brand-block">
      <span class="brand-square"></span>
      <div class="brand-name">ORIN VANTAGE</div>
    </div>
    <div class="divider"></div>
    <div class="contact">
      <h1 class="contact-name">Clara Jo Tsang</h1>
      <p class="contact-title">VP</p>
      <p class="address">APAC M&amp;A Operations<br>Orin Vantage Asia Pacific Limited<br>Unit 1407, K18<br>18 Tai Lok Shan Road<br>Hong Kong</p>
      <ul class="phones">
        <li><svg viewBox="0 0 24 24"><path d="M6.6 10.8a15.1 15.1 0 0 0 6.6 6.6l2.2-2.2c.3-.3.7-.4 1-.2 1.1.4 2.3.6 3.6.6.6 0 1 .4 1 1V20c0 .6-.4 1-1 1A17 17 0 0 1 3 4c0-.6.4-1 1-1h3.5c.6 0 1 .4 1 1 0 1.3.2 2.5.6 3.6.1.3 0 .7-.2 1z"/></svg>+852 2836 4100</li>
        <li><svg viewBox="0 0 24 24"><path d="M7 1h10a2 2 0 0 1 2 2v18a2 2 0 0 1-2 2H7a2 2 0 0 1-2-2V3a2 2 0 0 1 2-2zm0 3v14h10V4zm5 15.5a1 1 0 1 0 0 2 1 1 0 0 0 0-2z"/></svg>+852 6038 1742</li>
        <li><svg viewBox="0 0 24 24"><path d="M7 2h10v5H7zM4 8h16a2 2 0 0 1 2 2v7h-4v5H6v-5H2v-7a2 2 0 0 1 2-2zm4 8v4h8v-4z"/></svg>+852 2836 4177</li>
      </ul>
      <p class="voip">VOIP: 4158</p>
    </div>
    <svg class="stripe" viewBox="0 0 600 13" preserveAspectRatio="none">
      <polygon points="0,0 396,0 392,13 0,13" fill="#1fadd2"/>
      <polygon points="396,0 600,0 600,13 392,13" fill="#0e2742"/>
      <polygon points="400,0 600,0 600,13 396,13" fill="#f1f3f5"/>
    </svg>
  </section>

  <section class="card card-back" aria-label="Business card back">
    <div class="back-brand">
      <span class="back-square"></span>
      <div class="back-name">ORIN VANTAGE</div>
    </div>
    <p class="website">www.orinvantage.com</p>
  </section>
</main>
</body>
</html>
```